Inspirational Quotes Poster Set

Brookloft is a stylish coworking space, which has a design-oriented vintage look from the 60's with an industrial touch (www.brookloft-example.com) Brookloft Quote Poster Set of 16 posters. The poster should be typo oriented and rather simple. Reflecting a bit the clean billboard design from the sixties. Minimal / simple graphical elements

Target Market(s)

Startups and Entrepreneurs

Industry/Entity Type

Startup

Font styles to use
Sans Serif

Colors

Designer to choose colors to be used in the design.

Requirements
Must have
• Posters need to be on and very stylish

```html
<!DOCTYPE html>
<html lang="en">
<head>
<meta charset="utf-8">
<title>Brookloft Quote Poster Set – Doing Things</title>
<link rel="stylesheet" href="https://fonts.googleapis.com/css2?family=Schibsted+Grotesk:wght@700;800&display=swap">
<style>
  :root {
    --poster-red: #bd1421;
    --paper-white: #ffffff;
    --type-red: #bd1421;
  }
  * { margin: 0; padding: 0; box-sizing: border-box; }
  html, body {
    width: 801px;
    height: 1200px;
    overflow: hidden;
    background: var(--paper-white);
  }
  .poster {
    position: relative;
    width: 801px;
    height: 1200px;
    overflow: hidden;
    background: var(--paper-white);
    font-family: "Schibsted Grotesk", "Helvetica Neue", Arial, sans-serif;
  }
  .poster__band {
    position: absolute;
    left: 0;
    top: 262px;
    width: 801px;
    height: 938px;
    background: var(--poster-red);
  }
  .quote-lead {
    position: absolute;
    left: 32px;
    color: var(--type-red);
    font-weight: 800;
    font-size: 54px;
    line-height: 1;
    letter-spacing: -0.035em;
    white-space: nowrap;
  }
  .quote-lead--first { top: 160px; }
  .quote-lead--second { top: 207px; }
  .quote-punch {
    position: absolute;
    color: var(--paper-white);
    font-weight: 800;
    font-size: 292px;
    line-height: 1;
    letter-spacing: -0.06em;
    white-space: nowrap;
  }
  .quote-punch--doing { left: 18px; top: 228px; }
  .quote-punch--things { left: -12px; top: 477px; }
  .attribution {
    position: absolute;
    left: 70px;
    top: 1012px;
    color: var(--paper-white);
    font-weight: 700;
    font-size: 22px;
    line-height: 28px;
    letter-spacing: 0.02em;
  }
  .brand-name {
    position: absolute;
    left: 70px;
    top: 1098px;
    color: var(--paper-white);
    font-weight: 800;
    font-size: 50px;
    line-height: 1;
    letter-spacing: -0.03em;
  }
</style>
</head>
<body>
  <main class="poster">
    <div class="poster__band"></div>
    <p class="quote-lead quote-lead--first">we have a strategic plan</p>
    <p class="quote-lead quote-lead--second">it’s called</p>
    <p class="quote-punch quote-punch--doing">doing</p>
    <p class="quote-punch quote-punch--things">things</p>
    <p class="attribution">Harlan Keel,<br>Co Founder &amp; CEO Bluecrest Airlines</p>
    <p class="brand-name">Brookloft</p>
  </main>
</body>
</html>
```